Brookvale Building Company - advertisement poster

I am looking to print some canvas signs to advertise my general contracting company, Brookvale Building Company. The sign will measure 6' long x 3' high so the size should match that ratio. I already have a logo icon, which is the Letter 'B' and some trees that I would like to incorporate, see attached. I would also like the to have the following information listed:
1) phone number: 831-555-0172
2) email: brookvalebuildingcompany@mailnest.example
3) website: brookvalebuildingcompany.example
4) Lic#4826130
5) I want to use this text: "BUILD WITH THE B-CREW!"

The ad should be relatively simple and clean. Black and Green are my company colors. I am open to creative ideas!

Target Market(s)

People looking to renovate their homes

Industry/Entity Type

Construction

Colors
59FF00
82FF00
B8FF75
E3FFCB
F4FFEA

Requirements
Must have
• Must have my company logo
Should not have
• No photos or complex graphics

```html
<!DOCTYPE html>
<html lang="en">
<head>
<meta charset="utf-8">
<title>Brookvale Building Company – Sign</title>
<link rel="stylesheet" href="https://fonts.googleapis.com/css2?family=Orbitron:wght@600;800;900&family=Exo+2:wght@300&display=swap">
<style>
  :root {
    --page: #ffffff;
    --panel-top: #353535;
    --panel-band: #212223;
    --panel-deep: #121314;
    --panel-base: #070808;
    --green: #72b545;
    --white: #ffffff;
  }
  * { box-sizing: border-box; margin: 0; padding: 0; }
  html, body {
    width: 1200px;
    height: 705px;
    overflow: hidden;
    background: var(--page);
  }
  .sign {
    position: absolute;
    left: 52px;
    top: 74px;
    width: 1096px;
    height: 548px;
    overflow: hidden;
    color: var(--white);
  }
  .sign__backdrop {
    position: absolute;
    inset: 0;
    width: 100%;
    height: 100%;
  }
  .headline {
    position: absolute;
    top: 64px;
    left: 0;
    width: 100%;
    text-align: center;
    font-family: "Orbitron", sans-serif;
    font-weight: 800;
    font-size: 47px;
    letter-spacing: 1px;
    line-height: 1;
  }
  .brand {
    position: absolute;
    top: 160px;
    left: 0;
    width: 100%;
    display: flex;
    flex-direction: column;
    align-items: center;
  }
  .brand__mark {
    width: 104px;
    height: 104px;
    background: var(--green);
    margin-bottom: 40px;
  }
  .brand__name {
    font-family: "Orbitron", sans-serif;
    font-weight: 800;
    color: var(--white);
    text-align: center;
    line-height: 1;
  }
  .brand__name-main {
    display: block;
    font-size: 42px;
    letter-spacing: 1px;
  }
  .brand__name-sub {
    display: block;
    margin-top: 10px;
    font-size: 17px;
    letter-spacing: 11px;
  }
  .phone {
    position: absolute;
    top: 404px;
    left: 0;
    width: 100%;
    display: flex;
    justify-content: center;
    align-items: center;
    gap: 18px;
  }
  .phone__icon { width: 36px; height: 36px; }
  .phone__number {
    font-family: "Orbitron", sans-serif;
    font-weight: 900;
    font-size: 44px;
    letter-spacing: 2px;
    line-height: 1;
  }
  .contacts {
    position: absolute;
    top: 493px;
    left: 47px;
    right: 47px;
    display: flex;
    justify-content: space-between;
    align-items: center;
  }
  .contact {
    display: flex;
    align-items: center;
    gap: 10px;
    font-family: "Exo 2", sans-serif;
    font-weight: 300;
    font-size: 22px;
    line-height: 1;
  }
  .contact__icon { width: 20px; height: 20px; flex: none; }
</style>
</head>
<body>
  <main class="sign">
    <svg class="sign__backdrop" viewBox="0 0 2302 1151" preserveAspectRatio="none" aria-hidden="true">
      <rect width="2302" height="1151" fill="var(--panel-top)"/>
      <polygon points="0,226 1151,743 2302,226 2302,1151 0,1151" fill="var(--panel-band)"/>
      <polygon points="0,549 1151,887 2302,549 2302,1151 0,1151" fill="var(--panel-deep)"/>
      <polygon points="271,1151 1151,836 2021,1151" fill="var(--panel-base)" opacity="0.7"/>
    </svg>

    <h1 class="headline">BUILD WITH THE B-CREW!</h1>

    <div class="brand">
      <div class="brand__mark"></div>
      <p class="brand__name">
        <span class="brand__name-main">BROOKVALE</span>
        <span class="brand__name-sub">BUILDING COMPANY</span>
      </p>
    </div>

    <div class="phone">
      <svg class="phone__icon" viewBox="0 0 36 36" aria-hidden="true">
        <circle cx="18" cy="18" r="16.5" fill="none" stroke="var(--green)" stroke-width="1.6"/>
        <path d="M11.5 10.5c1-1 2-1 2.7 0l1.6 2.2c.5.7.4 1.5-.3 2.1l-.8.7c.8 1.8 2.3 3.4 4.1 4.2l.7-.8c.6-.7 1.4-.8 2.1-.3l2.2 1.6c1 .7 1 1.7 0 2.7-1.3 1.4-3 1.6-5 .7-3.4-1.6-6-4.2-7.6-7.6-.9-2-.6-3.7.3-5.5z" fill="var(--green)"/>
      </svg>
      <span class="phone__number">831-555-0172</span>
    </div>

    <div class="contacts">
      <p class="contact contact--email">
        <svg class="contact__icon" viewBox="0 0 20 20" aria-hidden="true">
          <rect x="1.5" y="3.5" width="17" height="13" rx="2.5" fill="none" stroke="var(--green)" stroke-width="2"/>
          <path d="M4 7l6 4 6-4" fill="none" stroke="var(--green)" stroke-width="2"/>
        </svg>
        <span>brookvalebuildingcompany@mailnest.example</span>
      </p>
      <p class="contact contact--web">
        <svg class="contact__icon" viewBox="0 0 20 20" aria-hidden="true">
          <circle cx="10" cy="10" r="8.5" fill="none" stroke="var(--green)" stroke-width="2"/>
          <ellipse cx="10" cy="10" rx="3.5" ry="8.5" fill="none" stroke="var(--green)" stroke-width="1.6"/>
          <path d="M1.5 10h17" stroke="var(--green)" stroke-width="1.6"/>
        </svg>
        <span>brookvalebuildingcompany.example</span>
      </p>
    </div>
  </main>
</body>
</html>
```